Baby Cloth Business Needs a Web Design

We need a web design for a new company that produces and sells baby sleeping bags. We use kelvoTrade (demo.kelvotrade.example) e-commerce software which we need a new design for that represents our products better. We would like to see designs that use simple and clean elements, playful layout with big pictures and emphasis on typography. We already have a logo that is "fresh" apple green so we would like colors that go well with that.
We use the following pages/features:
- Home page (with newsletter, chatterbook link and contact us link)
- Category page (no search needed)
- Product details page (with share)
- User pages (register, login, my account)
- Shopping cart with all its pages (about 6-7)
- Static pages (3 pages: contact us, about us, conditions of use).

We need designs in the form of PSD

Target Market(s)

Primary: mothers 25-45; secondary: women 20-60 who buy it as gift

Industry/Entity Type

Business

Requirements
Must have
• Since the site uses kelvoTrade no other data can be added beside those already exist on site.
Nice to have
• We have photos taken for this site (sample attached) and would be nice to show them in big sizes. We would like to see imaginative, playful elements that appear several places throughout the site. Logo contains a small baby foot which could leave footprints here and there.

We like these sites (and what):
- http://www.pelora.example/13-organic-bamboo-cotton-baby-essentials (simple, nice but too gray)
- http://www.quindeco.example/ (logo placement, menu, background)
- http://www.tervalo.example/
- http://www.brelt.example/website-template/view/html/baby-clothes?originUrl=http%3A%2F%2Fwww.brelt.example%2Fwebsite%2Ftemplates%2Fhtml%2Fonline-shop%2F2&galleryDocIndex=0 (layout, image sizes)
- http://themes.fashion.kel-layouts.example/?isOpen=false&;t_r=true (layout)
Should not have
• We do not use forum, blog, new products, manufacturers, popular tags, polls, search from kelvoTrade.

```html
<!DOCTYPE html>
<html lang="en">
<head>
<meta charset="utf-8">
<title>Snugpod – Home</title>
<link href="https://fonts.googleapis.com/css2?family=Arimo:wght@400;700&family=Comfortaa:wght@400&display=swap" rel="stylesheet">
<style>
:root{
  --green:#7ab83c;
  --green-light:#a6d26f;
  --green-dark:#5f9a28;
  --text:#444;
  --muted:#777;
  --line:#dcdcdc;
  --sky:#d7e8f5;
  --dark:#2b2b2b;
  --price:#c0392b;
  --btn:#8c8c8c;
  --hero:#ad9f8b;
}
*{box-sizing:border-box;margin:0;padding:0}
html,body{width:812px;height:1200px;overflow:hidden}
body{font-family:"Arimo",Arial,sans-serif;color:var(--text);font-size:9px;
  background:linear-gradient(#d9e9f6 0,#eef5fb 900px,#f4f8fb 1150px);position:relative}
.abs{position:absolute}
.top-links{right:70px;top:10px;font-size:10px;font-weight:700;color:#333;letter-spacing:.2px}
.top-links span{margin:0 6px;color:#555}
.sheet{left:60px;top:30px;width:691px;height:967px;background:#fff;border-radius:4px}
.logo{left:72px;top:44px;font-family:"Comfortaa",sans-serif;color:var(--green);font-size:34px;line-height:1}
.tagline{left:108px;top:115px;font-size:6.5px;color:var(--green)}
.cart{left:420px;top:56px;width:170px;height:54px;border:1px solid #ccc;border-radius:3px}
.cart-label{left:18px;top:9px;font-size:10px;font-weight:700;color:#555}
.cart-icon{left:22px;top:24px}
.cart-divider{left:76px;top:6px;width:1px;height:40px;background:#ddd}
.cart-info{left:78px;top:8px;font-size:8px;line-height:15px;color:#333}
.cart-info .links{color:var(--muted)}
.currency{left:597px;top:56px;width:143px;height:19px;border:1px solid #ccc;font-size:7.5px;color:#666;padding:4px 8px}
.flag{left:76px;top:4px;width:14px;height:10px;background:#b22;border:1px solid #ddd}
.caret{right:7px;top:7px;border:3.5px solid transparent;border-top-color:#777}
.chat{left:597px;top:82px;width:143px;height:27px;background:linear-gradient(#4a4a4a,#222);color:#eee;font-size:10px;font-weight:700;padding:8px 0 0 45px}
.chat svg{position:absolute;left:20px;top:6px}
.nav{left:70px;top:143px;width:671px;height:36px;border-top:1px solid var(--green-light);border-bottom:1px solid var(--green-light);display:flex;align-items:center;justify-content:space-between;padding:0 26px 0 12px;font-size:10px;color:#333}
.nav .active{background:var(--green);color:#fff;padding:5px 10px;border-radius:2px}
.hero{left:70px;top:183px;width:671px;height:278px;background:var(--hero)}
.hero-photo{left:0;top:0;width:380px;height:278px;background:linear-gradient(135deg,#a06a3c 0,#c89a6a 40%,#7fcbd8 75%,#b8a995 100%)}
.hero-title{left:403px;top:78px;font-size:18px;font-weight:700;color:#fff;letter-spacing:.4px}
.hero-text{left:403px;top:106px;width:242px;font-size:9.5px;line-height:15.5px;color:#fff;text-align:justify}
.order{left:403px;top:166px;width:111px;height:29px;background:#fff;border-radius:2px;font-size:13px;font-weight:700;color:#555;padding:7px 0 0 9px}
.order i{position:absolute;right:9px;top:7px;width:16px;height:16px;border-radius:50%;background:#555}
.order i::after{content:"";position:absolute;left:5px;top:4.5px;border:3.5px solid transparent;border-left:4.5px solid #fff}
.info{top:472px;width:217px;height:104px;border:1px solid var(--line);padding:6px 9px}
.info h2{font-size:14px;color:var(--green);margin-bottom:6px}
.info p{font-size:8.8px;line-height:14.3px;text-align:justify;color:#333}
.info p.quote{font-style:italic}
.more{left:9px;bottom:8px;width:197px;height:19px;background:#eee;border-radius:2px;text-align:right;padding:5px 12px 0 0;font-size:7.5px;color:#777}
.products-bar{left:70px;top:586px;width:671px;height:37px;background:linear-gradient(#9fd069,#7fbb49);color:#fff;font-size:14px;font-weight:700;padding:11px 12px}
.products-bar i{position:absolute;right:12px;top:11px;width:15px;height:15px;border-radius:50%;background:var(--green-dark)}
.products-bar i::after{content:"";position:absolute;left:5px;top:4px;border:3.5px solid transparent;border-left:4px solid #fff}
.card{width:158px;height:170px;border:1px solid #e6e6e6;border-radius:3px;background:#fbfbfb}
.card .thumb{left:8px;top:8px;width:141px;height:92px;border:1px solid #e4e4e4}
.card .name{left:11px;top:108px;font-size:9px;color:#777}
.card .price{left:11px;top:125px;font-size:9.5px;color:var(--price)}
.card .btn{top:142px;width:69px;height:21px;background:linear-gradient(#9a9a9a,#777);color:#fff;font-size:9px;border-radius:2px;padding:5px 0 0 9px}
.card .buy{left:8px}.card .view{left:79px}
.footer h3{font-size:11.5px;font-weight:400;color:#333}
.ql{top:1035px;font-size:8px;color:#666;line-height:19.8px;list-style:none}
.ql li::before{content:"• ";color:#999}
.vsep{top:1005px;width:1px;height:140px;background:#ddd}
.field{left:424px;width:154px;height:19px;border:1px solid #ccc;font-size:7.5px;color:#333;padding:5px 10px}
.submit{left:530px;top:1092px;width:48px;height:19px;background:linear-gradient(#8d8d8d,#6b6b6b);color:#fff;font-size:10px;font-weight:700;padding:4px 0 0 6px}
.pay{top:1127px;width:21px;height:13px;border:1px solid #ccc;border-radius:2px;background:linear-gradient(#fff,#e8e8e8)}
.social{left:611px;font-size:8.5px;color:#777}
.social i{position:absolute;left:0;top:-5px;width:19px;height:19px;border-radius:2px}
.social span{position:absolute;left:35px;top:0;white-space:nowrap}
.social b{font-weight:400;font-size:10px}
.bottom{left:0;top:1156px;width:812px;height:44px;background:var(--dark);color:#aaa;font-size:8px;text-align:center;padding-top:18px}
</style>
</head>
<body>
<div class="abs top-links">REGISTER<span>::</span>LOGIN</div>
<div class="abs sheet"></div>

<header>
  <div class="abs logo">Snugpod</div>
  <div class="abs tagline">smart sleeping bag for babies and kids</div>
  <div class="abs cart">
    <div class="abs cart-label">My Cart</div>
    <svg class="abs cart-icon" width="24" height="20" viewBox="0 0 24 20"><path d="M1 2h4l3 11h12l2-8H7" fill="none" stroke="#666" stroke-width="1.8"/><circle cx="10" cy="17" r="1.8" fill="#666"/><circle cx="18" cy="17" r="1.8" fill="#666"/></svg>
    <div class="abs cart-divider"></div>
    <div class="abs cart-info">(0) items in your cart<br>Total - $ 00.00<br><span class="links">My Account &nbsp;|&nbsp; My List</span></div>
  </div>
  <div class="abs currency">Currency &nbsp;- &nbsp;US $<span class="abs flag"></span><span class="abs caret"></span></div>
  <div class="abs chat"><svg width="20" height="14" viewBox="0 0 20 14"><ellipse cx="8" cy="6" rx="7.5" ry="5.5" fill="#ccc"/><ellipse cx="13" cy="8" rx="6" ry="4.5" fill="#999"/></svg>Live Chat with us</div>
  <nav class="abs nav"><span class="active">HOME</span><span>ABOUT US</span><span>PRODUCTS</span><span>NEW BORNS</span><span>TESTIMONIALS</span><span>CONTACT US</span><span>FAQS</span></nav>
</header>

<section class="abs hero">
  <div class="abs hero-photo" role="img" aria-label="Photo of a smiling toddler in a polka-dot bib sitting in a wooden chair"></div>
  <h1 class="abs hero-title">SMOOTH &nbsp;AND SOFT BAGS</h1>
  <p class="abs hero-text">Nulla suscipit bibendum lacinia. Quisque in viverra metus. Suspendisse blandit erat nec faucibus pretium. Ut faucibus accumsan eros et viverra.</p>
  <div class="abs order">Order Now<i></i></div>
</section>

<section class="abs info" style="left:70px"><h2>About us</h2><p>Pellentesque sollicitudin ullamcorper sapien vel faucibus. Nullam at nunc in sem fermentum ornare in ac enim aenean consectetur.</p><div class="abs more">VIEW MORE &nbsp;»</div></section>
<section class="abs info" style="left:297px"><h2>Why us</h2><p>Pellentesque sollicitudin ullamcorper sapien vel faucibus. Nullam at nunc in sem fermentum ornare in ac enim aenean consectetur.</p><div class="abs more">VIEW MORE &nbsp;»</div></section>
<section class="abs info" style="left:524px"><h2>Testimonials</h2><p class="quote">“ Pellentesque sollicitudin ullamcorper sapien vel faucibus. Nullam at nunc in sem fermentum ornare in ac enim aenean consectetur ”</p><div class="abs more">VIEW MORE &nbsp;»</div></section>

<div class="abs products-bar">Our Products<i></i></div>

<div class="abs card" style="left:70px;top:632px"><div class="abs thumb" role="img" aria-label="Baby in a pale blue sleeping bag" style="background:linear-gradient(#eef3f6,#dfe8ee)"></div><div class="abs name">Curabitur laoreet aliquam</div><div class="abs price">Price : $199</div><div class="abs btn buy">›› Buy Now</div><div class="abs btn view">›› View more</div></div>
<div class="abs card" style="left:241px;top:632px"><div class="abs thumb" role="img" aria-label="Lilac baby carry cot" style="background:radial-gradient(circle,#c9a6cf 0,#fff 70%)"></div><div class="abs name">Curabitur laoreet aliquam</div><div class="abs price">Price : $199</div><div class="abs btn buy">›› Buy Now</div><div class="abs btn view">›› View more</div></div>
<div class="abs card" style="left:412px;top:632px"><div class="abs thumb" role="img" aria-label="Baby in a light blue sleep sack" style="background:radial-gradient(circle,#c3d6e6 0,#fff 70%)"></div><div class="abs name">Curabitur laoreet aliquam</div><div class="abs price">Price : $199</div><div class="abs btn buy">›› Buy Now</div><div class="abs btn view">›› View more</div></div>
<div class="abs card" style="left:583px;top:632px"><div class="abs thumb" role="img" aria-label="Smartphone product image" style="background:radial-gradient(circle,#555 0,#fff 55%)"></div><div class="abs name">Curabitur laoreet aliquam</div><div class="abs price">Price : $199</div><div class="abs btn buy">›› Buy Now</div><div class="abs btn view">›› View more</div></div>

<div class="abs card" style="left:70px;top:816px"><div class="abs thumb" role="img" aria-label="Pink and blue baby snowsuits" style="background:radial-gradient(circle,#e6b7d0 0,#fff 70%)"></div><div class="abs name">Curabitur laoreet aliquam</div><div class="abs price">Price : $199</div><div class="abs btn buy">›› Buy Now</div><div class="abs btn view">›› View more</div></div>
<div class="abs card" style="left:241px;top:816px"><div class="abs thumb" role="img" aria-label="White quilted baby blanket" style="background:radial-gradient(circle,#ddd 0,#fff 70%)"></div><div class="abs name">Curabitur laoreet aliquam</div><div class="abs price">Price : $199</div><div class="abs btn buy">›› Buy Now</div><div class="abs btn view">›› View more</div></div>
<div class="abs card" style="left:412px;top:816px"><div class="abs thumb" role="img" aria-label="Beige sleeping bag" style="background:radial-gradient(circle,#d6a995 0,#fff 55%)"></div><div class="abs name">Curabitur laoreet aliquam</div><div class="abs price">Price : $199</div><div class="abs btn buy">›› Buy Now</div><div class="abs btn view">›› View more</div></div>
<div class="abs card" style="left:583px;top:816px"><div class="abs thumb" role="img" aria-label="Folded printed baby wrap" style="background:radial-gradient(circle,#cfdbe6 0,#fff 60%)"></div><div class="abs name">Curabitur laoreet aliquam</div><div class="abs price">Price : $199</div><div class="abs btn buy">›› Buy Now</div><div class="abs btn view">›› View more</div></div>

<footer class="footer">
  <h3 class="abs" style="left:62px;top:1006px">Quick Links</h3>
  <ul class="abs ql" style="left:63px"><li>Integer lobortis</li><li>Curabitur ac</li><li>Phasellus tellus nisl</li><li>Aenean fringilla</li><li>Vestibulum</li><li>Aliquam commodo</li></ul>
  <ul class="abs ql" style="left:184px"><li>Integer lobortis</li><li>Curabitur ac</li><li>Phasellus tellus nisl</li><li>Aenean fringilla</li><li>Vestibulum</li><li>Aliquam commodo</li></ul>
  <ul class="abs ql" style="left:304px"><li>Integer lobortis</li><li>Curabitur ac</li><li>Phasellus tellus nisl</li><li>Aenean fringilla</li><li>Vestibulum</li><li>Aliquam commodo</li></ul>
  <div class="abs vsep" style="left:411px"></div>
  <h3 class="abs" style="left:424px;top:1006px">Email Signup</h3>
  <div class="abs field" style="top:1035px">Name</div>
  <div class="abs field" style="top:1064px">Email ID</div>
  <div class="abs submit">SUBMIT</div>
  <div class="abs pay" style="left:452px"></div><div class="abs pay" style="left:478px"></div><div class="abs pay" style="left:504px"></div><div class="abs pay" style="left:530px"></div><div class="abs pay" style="left:555px"></div>
  <div class="abs vsep" style="left:598px"></div>
  <h3 class="abs" style="left:612px;top:1006px">Connect with us</h3>
  <div class="abs social" style="top:1039px"><i style="background:#3b5a98"></i><span>Join with us on &nbsp;<b style="color:#3b5a98">Chatterbook</b></span></div>
  <div class="abs social" style="top:1067px"><i style="background:#3fb3e3"></i><span>Follow us on &nbsp;<b style="color:#3fb3e3">Chirpline</b></span></div>
  <div class="abs social" style="top:1095px"><i style="background:#1a6ea6"></i><span>Share on &nbsp;<b style="color:#1a6ea6">Linkwork</b></span></div>
  <div class="abs social" style="top:1123px"><i style="background:#c9302c"></i><span>Watch on &nbsp;<b style="color:#222">Vidora</b></span></div>
  <div class="abs bottom">Copyright &nbsp;© &nbsp;2013 &nbsp;&nbsp;www.snugpod.example &nbsp;&nbsp;All rights reserved.</div>
</footer>
</body>
</html>
```